Indy Film Production Company/Studio

We need a business card designed from an existing logo. We are a digital studio/production company that caters to creating genre entertainment, like Action, Horror, and martial arts. The card along with the logo will be used to Brand the company from letter heads to banners. The design will also be used for postcards and Brochures. It should be professional and masculine.
Updates

Thank you to all the designers who have participated. I'm narrowing down who it will be. Thank you again.

Target Market(s)

Investors, Networks, Producers, and actors

Industry/Entity Type

Film Production

Contact Information for Business Card

Teodoro Valbuena
Producer/Writer/Director
www.kestrelpicturehouse.example

Requirements
Must have
• Website address, Facebook icon and Twitter icon possibly in the back of the card.
Nice to have
• Logline of Company: Follow The Action.

```html
<!DOCTYPE html>
<html lang="en">
<head>
<meta charset="utf-8">
<title>Kestrel Picture House – Business Card</title>
<link href="https://fonts.googleapis.com/css2?family=Arimo:wght@400;700&display=swap" rel="stylesheet">
<style>
  :root {
    --stage: #3a3a3c;
    --red: #e3161f;
    --red-deep: #b30f16;
    --white: #ffffff;
    --ink: #2b2b2b;
    --swoosh: #333333;
  }
  * { box-sizing: border-box; margin: 0; padding: 0; }
  html, body {
    width: 1200px; height: 950px; overflow: hidden;
    background: var(--stage);
    font-family: "Arimo", Arial, sans-serif;
  }
  .stage {
    width: 1200px; height: 950px;
    display: flex; flex-direction: column; align-items: center; justify-content: center;
    gap: 50px;
  }
  .card {
    position: relative;
    width: 700px; height: 400px;
    overflow: hidden;
    box-shadow: 0 10px 30px rgba(0,0,0,.45);
  }

  /* Back of card */
  .card--back {
    background: linear-gradient(135deg, var(--red) 0%, var(--red) 55%, var(--red-deep) 100%);
    color: var(--white);
  }
  .social {
    position: absolute; top: 22px; right: 24px;
    display: flex; gap: 6px;
  }
  .social__square {
    width: 26px; height: 26px; background: var(--white); opacity: .9;
  }
  .back__brand {
    position: absolute; left: 0; right: 0; top: 150px;
    text-align: center;
    font-weight: 700; font-size: 44px; letter-spacing: 3px;
    text-transform: uppercase; color: var(--white);
  }
  .back__web {
    position: absolute; left: 0; right: 0; top: 232px;
    text-align: center;
    font-size: 20px; letter-spacing: 2px; color: var(--white);
  }

  /* Front of card */
  .card--front { background: var(--red); }
  .front__shape { position: absolute; inset: 0; }
  .front__name {
    position: absolute; left: 34px; top: 30px;
    font-weight: 700; font-size: 26px; color: var(--red);
  }
  .front__role {
    position: absolute; left: 34px; top: 64px;
    font-size: 18px; color: var(--ink);
  }
  .front__brand {
    position: absolute; left: 34px; top: 130px;
    font-weight: 700; font-size: 40px; line-height: 1.05;
    letter-spacing: 2px; text-transform: uppercase; color: var(--red);
  }
  .contact {
    position: absolute; right: 28px; bottom: 30px;
    list-style: none;
    display: flex; flex-direction: column; align-items: flex-end; gap: 7px;
    color: var(--white); font-size: 18px;
  }
  .contact__item { display: flex; align-items: center; gap: 10px; }
  .contact__icon { width: 18px; height: 18px; flex: none; }
</style>
</head>
<body>
<main class="stage">

  <section class="card card--back" aria-label="Back of business card">
    <div class="social" aria-label="Social profiles">
      <span class="social__square"></span>
      <span class="social__square"></span>
    </div>
    <p class="back__brand">Kestrel Picture House</p>
    <p class="back__web">www.kestrelpicturehouse.example</p>
  </section>

  <section class="card card--front" aria-label="Front of business card">
    <svg class="front__shape" viewBox="0 0 700 400" preserveAspectRatio="none" aria-hidden="true">
      <path d="M0 0 H700 V190 Q420 330 0 250 Z" fill="#ffffff"/>
      <path d="M0 250 Q420 330 700 190 L700 198 Q420 342 0 262 Z" fill="#333333"/>
    </svg>
    <p class="front__name">Teodoro Valbuena</p>
    <p class="front__role">Producer/Writer/Director</p>
    <p class="front__brand">Kestrel<br>Picture House</p>
    <ul class="contact">
      <li class="contact__item">555 0142 7788
        <svg class="contact__icon" viewBox="0 0 24 24" aria-hidden="true"><path fill="#fff" d="M6.6 10.8a15.1 15.1 0 0 0 6.6 6.6l2.2-2.2c.3-.3.7-.4 1-.2 1.1.4 2.3.6 3.6.6.6 0 1 .4 1 1V20c0 .6-.4 1-1 1A17 17 0 0 1 3 4c0-.6.4-1 1-1h3.5c.6 0 1 .4 1 1 0 1.3.2 2.5.6 3.6.1.3 0 .7-.2 1z"/></svg>
      </li>
      <li class="contact__item">teo@kestrelpicturehouse.example
        <svg class="contact__icon" viewBox="0 0 24 24" aria-hidden="true"><rect x="2" y="5" width="20" height="14" fill="#fff"/><path d="M2 5l10 8 10-8" fill="none" stroke="#e3161f" stroke-width="1.6"/></svg>
      </li>
      <li class="contact__item">www.kestrelpicturehouse.example
        <svg class="contact__icon" viewBox="0 0 24 24" aria-hidden="true"><circle cx="12" cy="12" r="10" fill="#fff"/><path d="M2 12h20M12 2c3 3 3 17 0 20M12 2c-3 3-3 17 0 20" fill="none" stroke="#e3161f" stroke-width="1.4"/></svg>
      </li>
    </ul>
  </section>

</main>
</body>
</html>
```